I need a book cover (front and back) for a book I wrote called "7 Laws of Polish: A Closet Map for Triumph".

The short version of the book can be found online here: https://filebin.example.net/file/d/7KqPzR2mXwT9bLcN4vHs8YdJ3fGeA0uWi/view

I'm working on expanding this into a real book (100+ pages, with images), and putting it on Pellora.

I'm the author, Joel Mackworth. I was named "Sharpest Gent of the Nation" by Dapperly Journal, and I would like to add that to the cover for credibility.

My website "About Page" has more info about me and my business Threadwell House: https://threadwellhouse.example/pages/about-us

I also attached the first version of the cover I made using Canva.

I have LOTS of images, if you need some (mannequins, models, garments, etc). See our website's blog for more ideas of the images we have: https://threadwellhouse.example/blogs/news

```html
<!DOCTYPE html>
<html lang="en">
<head>
<meta charset="utf-8">
<title>7 Laws of Polish — Book Cover</title>
<link rel="stylesheet" href="https://fonts.googleapis.com/css2?family=Bodoni+Moda:ital,opsz,wght@0,6..96,400;1,6..96,400&family=Tinos:ital,wght@0,400;1,400;1,700&family=Jost:wght@500&display=swap">
<style>
  :root {
    --backdrop: #5a5a5a;
    --cover: #c3a48b;
    --cover-deep: #a88a72;
    --ink: #1f1a17;
    --ink-soft: #2e2621;
    --rule-gold: #c9a24a;
    --figure-tone: #8d7463;
    --portrait-tone: #7a5a4e;
    --suit-tone: #2a2421;
  }
  * { box-sizing: border-box; margin: 0; padding: 0; }
  html, body {
    width: 1200px; height: 740px; overflow: hidden;
    background: var(--backdrop);
  }
  .canvas { position: relative; width: 1200px; height: 740px; }

  .cover {
    position: absolute; top: 80px;
    width: 390px; height: 580px;
    background: var(--cover);
    overflow: hidden;
  }
  .back  { left: 95px; }
  .spine {
    position: absolute; top: 80px; left: 535px;
    width: 60px; height: 580px;
    background: var(--cover);
    overflow: hidden;
  }
  .front { left: 715px; }

  /* ---------- back cover ---------- */
  .back-figure {
    position: absolute; left: 120px; top: 20px;
    width: 270px; height: 560px;
    background: radial-gradient(ellipse at 50% 40%, var(--figure-tone) 0%, rgba(141,116,99,0.35) 55%, rgba(195,164,139,0) 80%);
    opacity: 0.7;
  }
  .back-copy {
    position: absolute; left: 55px; top: 64px; width: 280px;
    font-family: "Tinos", "Times New Roman", serif;
    font-size: 8.4px; line-height: 1.3;
    color: var(--ink-soft); text-align: center;
  }
  .testimonial { margin-bottom: 5px; }
  .divider {
    width: 150px; height: 1px; margin: 0 auto 6px;
    background: var(--rule-gold);
  }
  .story p { margin-bottom: 4px; }
  .story .signoff { font-style: italic; font-weight: 700; }
  .author-portrait {
    width: 92px; height: 92px; border-radius: 50%;
    margin: 14px auto 24px;
    background: radial-gradient(circle at 50% 60%, var(--portrait-tone), #a4644f 75%);
  }
  .bio { margin-bottom: 6px; }

  /* ---------- spine ---------- */
  .spine-title {
    position: absolute; left: 30px; top: 20px;
    transform-origin: 0 0; transform: rotate(90deg) translateY(-50%);
    white-space: nowrap;
    font-family: "Bodoni Moda", "Didot", serif;
    font-size: 44px; line-height: 1; color: var(--ink);
    letter-spacing: -2px;
  }
  .spine-title span { display: inline-block; transform: scaleX(0.62); transform-origin: left center; }
  .spine-rule {
    position: absolute; left: 0; right: 0; top: 326px;
    height: 1px; background: var(--ink-soft); opacity: 0.5;
  }
  .spine-author {
    position: absolute; left: 30px; top: 340px;
    transform-origin: 0 0; transform: rotate(90deg) translateY(-50%);
    white-space: nowrap;
    font-family: "Jost", "Futura", sans-serif; font-weight: 500;
    font-size: 12px; letter-spacing: 3.2px; color: var(--ink-soft);
  }

  /* ---------- front cover ---------- */
  .accolade {
    position: absolute; top: 34px; left: 0; right: 0;
    text-align: center;
    font-family: "Tinos", "Times New Roman", serif; font-style: italic;
    font-size: 10px; line-height: 1.35; letter-spacing: 1px;
    color: var(--ink-soft);
  }
  .author-photo {
    position: absolute; left: 14px; top: 136px;
    width: 140px; height: 382px;
    background: linear-gradient(180deg, rgba(42,36,33,0) 0%, rgba(42,36,33,0.85) 12%, var(--suit-tone) 60%, rgba(42,36,33,0.7) 100%);
    border-radius: 40px 40px 6px 6px;
  }
  .title {
    position: absolute; left: 122px; top: 150px;
    font-family: "Bodoni Moda", "Didot", serif; font-weight: 400;
    color: var(--ink);
  }
  .title .line {
    display: block; position: absolute; white-space: nowrap;
    transform: scaleX(0.58); transform-origin: left top;
    line-height: 1;
  }
  .title .num    { top: 0;    left: 60px; font-size: 112px; }
  .title .laws   { top: 80px; left: 0;    font-size: 118px; letter-spacing: -4px; }
  .title .of     { top: 192px; left: 32px; font-size: 52px; }
  .title .polish { top: 192px; left: 0;  font-size: 118px; letter-spacing: -4px; }
  .title .of { z-index: 1; }
  .title .polish { left: 12px; top: 220px; }
  .front-author {
    position: absolute; right: 22px; bottom: 26px;
    font-family: "Jost", "Futura", sans-serif; font-weight: 500;
    font-size: 13px; letter-spacing: 2.6px; color: var(--ink);
  }
</style>
</head>
<body>
<main class="canvas">

  <section class="cover back" aria-label="Back cover">
    <div class="back-figure" role="img" aria-label="Faint photograph of a man in a hat and work shirt"></div>
    <div class="back-copy">
      <p class="testimonial">"TWH is an experience unlike any other. You have real experts (the best in the game) who work directly with you to pick the right clothes and make sure it all fits perfectly." -Grant, Connecticut</p>
      <div class="divider"></div>
      <p class="testimonial">"Working with Joel and TWH has truly been a life-changing experience. I can't recommend it enough. I went from no style to best-dressed at my company." -Wallace, California</p>
      <div class="divider"></div>
      <p class="testimonial">"After working with TWH I'm a whole new person. I'm so confident and put together... I don't even recognize the old me." -Marco, Texas</p>
      <div class="divider"></div>
      <div class="story">
        <p>In 2009 I was named “Sharpest Gent of the Nation” by Dapperly Journal and for the next 10 years I apprenticed with the premier bespoke tailor in New York City; fitting customers of all shapes and sizes and designing their wardrobes from top to bottom.</p>
        <p>People traveled from all over the world to get fitted by me in New York. That's when I realized that most people don't have access to a knowledgeable stylist or a reliable tailor.</p>
        <p class="signoff">This is why I created Threadwell House.</p>
      </div>
      <div class="author-portrait" role="img" aria-label="Round portrait photograph of the author"></div>
      <p class="bio">Joel Mackworth was named “Sharpest Gent of the Nation” by Dapperly Journal while studying psychology at Harlow University. He then trained to become a bespoke tailor and earned a degree in Menswear Design from the Meridian Institute of Design. After ten years of working with customers in New York City, Joel combined his experience in bespoke tailoring with his passion for teaching men how to dress for Joel lives in Toronto with his wife Elise and their daughter Mara where he works with customers from all over the world to improve their style and refine their wardrobes. success and created Threadwell House.</p>
      <div class="divider"></div>
    </div>
  </section>

  <section class="spine" aria-label="Spine">
    <div class="spine-title"><span>7 Laws of Polish</span></div>
    <div class="spine-rule"></div>
    <div class="spine-author">JOEL MACKWORTH</div>
  </section>

  <section class="cover front" aria-label="Front cover">
    <p class="accolade">“Sharpest Gent of the Nation”<br>by Dapperly Journal</p>
    <div class="author-photo" role="img" aria-label="Full-length photograph of the author standing in a dark suit and striped tie"></div>
    <h1 class="title">
      <span class="line num">7</span>
      <span class="line laws">Laws</span>
      <span class="line of">of</span>
      <span class="line polish">Polish</span>
    </h1>
    <p class="front-author">JOEL MACKWORTH</p>
  </section>

</main>
</body>
</html>
```